Business Card Design Project : Ridgeline Press

In preparation for market launch, Tamarind's Ridgeline Press require the development of a business card. Ridgeline Press is a Community online publishing web portal. We provide the the city of Whistler located in B.C. (Canada) business directories, News, Classified ads, News, Events and blogs etc.

The main focus of the brand is to help local businesses to corporate with their online advertisement and marketing. Meeting our clients face to face is a must (B2B).

Target Market(s)

The target market is B2B customers. Business Owners to Marketing, advertising Managers

Industry/Entity Type

Business

Requirements
Must have
• - The business card will be two sided.
the BACK side will have our logo which consist of (icon, url,slogan) submited. The logo will be middle and centred.

The FRONT side should have company details:

Company Legal Name: TAMARIND RIDGELINE MEDIA

Owen Farsk
Director of Sales & Marketing

www.tamarindridgeline.biz
owen@tamarindridgeline.biz

Phone: 604 317 8842
#2714 - 582 E. Halvern St.
Vancouver, B.C. V7K2R4 Canada
Nice to have
• - For the "FRONT" side of our business card. You can separate or re-arrange with our logo components (icon, logo,slogan). It does not have to be together.

Also our company legal name is rather long so arrange or organize the name in a way to make it shorter. Your experience and creativity will have to come in play.
Should not have
• should not have other colors beside logo color and black text (2 colors). Also nothing Three dimensional

```html
<!DOCTYPE html>
<html lang="en">
<head>
<meta charset="utf-8">
<title>Ridgeline Press – Business Card Options</title>
<link href="https://fonts.googleapis.com/css2?family=Questrial&family=Nunito+Sans:wght@400;700;800&family=Libre+Caslon+Display&display=swap" rel="stylesheet">
<style>
  :root {
    --brand-blue: #1484d6;
    --ink: #0d0d0d;
    --paper: #ffffff;
    --back-card: #8f8f8f;
    --back-edge: #4a4a4a;
    --label-line: #333333;
  }
  * { box-sizing: border-box; margin: 0; padding: 0; }
  html, body { width: 1200px; height: 917px; overflow: hidden; background: var(--paper); }
  .sheet { position: relative; width: 1200px; height: 917px; }

  .option { position: absolute; width: 580px; height: 340px; }
  .option-1 { left: 10px;  top: 24px; }
  .option-2 { left: 617px; top: 36px; }
  .option-3 { left: 16px;  top: 518px; }
  .option-4 { left: 622px; top: 518px; }

  .card-back {
    position: absolute; left: 0; top: 0; width: 562px; height: 320px;
    background: var(--back-card); border: 2px solid var(--back-edge);
    transform: translate(-8px, -8px) rotate(1.6deg); transform-origin: center;
  }
  .option-1 .card-back { transform: translate(4px, -4px) rotate(1.2deg); }

  .card-front {
    position: absolute; left: 0; top: 0; width: 562px; height: 320px;
    background: var(--brand-blue); overflow: hidden;
  }
  .option-1 .card-front { transform: rotate(-2.2deg); transform-origin: center; }

  .snow-band { position: absolute; inset: 0; width: 100%; height: 100%; }

  .company-name {
    position: absolute; right: 22px; top: 32px;
    font-family: "Questrial", sans-serif; font-size: 24px; color: var(--paper);
    letter-spacing: 0.2px; white-space: nowrap;
  }
  .company-name::before {
    content: ""; display: inline-block; width: 13px; height: 13px;
    border-radius: 50%; background: currentColor; margin-right: 8px; vertical-align: 1px;
  }
  .option-1 .company-name { color: var(--ink); }
  .slogan {
    position: absolute; right: 22px; top: 62px;
    font-family: "Questrial", sans-serif; font-size: 12px; letter-spacing: 3.2px;
    color: var(--paper); white-space: nowrap;
  }
  .slogan strong { font-family: "Nunito Sans", sans-serif; font-weight: 800; }
  .option-1 .slogan { color: var(--ink); }

  .person-name {
    position: absolute; left: 50px; top: 112px;
    font-family: "Libre Caslon Display", serif; font-size: 40px;
    color: transparent; -webkit-text-stroke: 1.3px var(--paper); white-space: nowrap;
  }
  .option-1 .person-name { -webkit-text-stroke-color: var(--ink); left: 46px; top: 106px; }

  .person-role {
    position: absolute; left: 50px; top: 166px;
    font-family: "Nunito Sans", sans-serif; font-weight: 800; font-size: 13px;
    color: var(--ink); letter-spacing: 0.3px; white-space: nowrap;
  }
  .option-1 .person-role { color: var(--paper); top: 160px; left: 46px; }

  .online {
    position: absolute; left: 50px; top: 226px;
    font-family: "Nunito Sans", sans-serif; font-size: 13px; line-height: 17px;
    color: var(--paper); letter-spacing: 0.2px; white-space: nowrap;
  }
  .online strong { font-weight: 800; }
  .option-1 .online { color: var(--ink); left: 46px; top: 218px; }

  .address {
    position: absolute; right: 16px; top: 258px; text-align: right;
    font-family: "Nunito Sans", sans-serif; font-weight: 800; font-size: 12px; line-height: 17px;
    color: var(--brand-blue); letter-spacing: 0.4px; white-space: nowrap;
  }
  .option-3 .address { color: var(--ink); }

  .option-number {
    position: absolute; width: 60px; height: 60px; border-radius: 50%;
    border: 2px solid var(--label-line);
    font-family: "Nunito Sans", sans-serif; font-size: 40px; line-height: 55px;
    text-align: center; color: var(--label-line);
  }
  .number-1 { left: 250px; top: 365px; }
  .number-2 { left: 854px; top: 378px; }
  .number-3 { left: 246px; top: 854px; }
  .number-4 { left: 859px; top: 854px; }
</style>
</head>
<body>
<main class="sheet">

  <section class="option option-1">
    <div class="card-back"></div>
    <div class="card-front">
      <svg class="snow-band" viewBox="0 0 562 320" preserveAspectRatio="none" aria-hidden="true">
        <path d="M0,272 C120,300 220,280 300,245 C360,220 400,228 430,214 C470,194 505,176 562,208 L562,320 L0,320 Z" fill="var(--paper)"/>
      </svg>
      <div class="company-name">Tamarind Ridgeline Press</div>
      <div class="slogan">Your <strong>information</strong> gateway</div>
      <div class="person-name">Owen Farsk</div>
      <div class="person-role">Director of Sales &amp; Marketing</div>
      <div class="online">www.<strong>tamarindridgeline</strong>.biz<br><strong>owen@tamarindridgeline</strong>.biz</div>
      <div class="address">Phone: 604 317 8842<br>#2714 - 582 E. Halvern St.<br>Vancouver, B.C. V7K2R4 Canada</div>
    </div>
  </section>

  <section class="option option-2">
    <div class="card-back"></div>
    <div class="card-front">
      <svg class="snow-band" viewBox="0 0 562 320" preserveAspectRatio="none" aria-hidden="true">
        <path d="M0,272 C120,300 220,280 300,245 C360,220 400,228 430,214 C470,194 505,176 562,208 L562,320 L0,320 Z" fill="var(--paper)"/>
      </svg>
      <div class="company-name">Tamarind Ridgeline Press</div>
      <div class="slogan">Your <strong>information</strong> gateway</div>
      <div class="person-name">Owen Farsk</div>
      <div class="person-role">Director of Sales &amp; Marketing</div>
      <div class="online">www.<strong>tamarindridgeline</strong>.biz<br><strong>owen@tamarindridgeline</strong>.biz</div>
      <div class="address">Phone: 604 317 8842<br>#2714 - 582 E. Halvern St.<br>Vancouver, B.C. V7K2R4 Canada</div>
    </div>
  </section>

  <section class="option option-3">
    <div class="card-back"></div>
    <div class="card-front">
      <svg class="snow-band" viewBox="0 0 562 320" preserveAspectRatio="none" aria-hidden="true">
        <path d="M0,272 C120,300 220,280 300,245 C360,220 400,228 430,214 C470,194 505,176 562,208 L562,320 L0,320 Z" fill="var(--paper)"/>
      </svg>
      <div class="company-name">Tamarind Ridgeline Press</div>
      <div class="slogan">Your <strong>information</strong> gateway</div>
      <div class="person-name">Owen Farsk</div>
      <div class="person-role">Director of Sales &amp; Marketing</div>
      <div class="online">www.<strong>tamarindridgeline</strong>.biz<br><strong>owen@tamarindridgeline</strong>.biz</div>
      <div class="address">Phone: 604 317 8842<br>#2714 - 582 E. Halvern St.<br>Vancouver, B.C. V7K2R4 Canada</div>
    </div>
  </section>

  <section class="option option-4">
    <div class="card-back"></div>
    <div class="card-front">
      <svg class="snow-band" viewBox="0 0 562 320" preserveAspectRatio="none" aria-hidden="true">
        <path d="M0,272 C120,300 220,280 300,245 C360,220 400,228 430,214 C470,194 505,176 562,208 L562,320 L0,320 Z" fill="var(--paper)"/>
      </svg>
      <div class="company-name">Tamarind Ridgeline Press</div>
      <div class="slogan">Your <strong>information</strong> gateway</div>
      <div class="person-name">Owen Farsk</div>
      <div class="person-role">Director of Sales &amp; Marketing</div>
      <div class="online">www.<strong>tamarindridgeline</strong>.biz<br><strong>owen@tamarindridgeline</strong>.biz</div>
      <div class="address">Phone: 604 317 8842<br>#2714 - 582 E. Halvern St.<br>Vancouver, B.C. V7K2R4 Canada</div>
    </div>
  </section>

  <div class="option-number number-1">1</div>
  <div class="option-number number-2">2</div>
  <div class="option-number number-3">3</div>
  <div class="option-number number-4">4</div>

</main>
</body>
</html>
```